Dunmore Roofing

Want a professional looking business card

Industry/Entity Type

Business

Contact Information for Business Card

Paul Dunmore ( Owner) paul@dunmoreroofing-example.com, www.dunmoreroofing-example.com, Adress: 4172 Township road 43 Plantagenet,ON K9X4T2

```html
<!DOCTYPE html>
<html lang="en">
<head>
<meta charset="utf-8">
<title>Dunmore Roofing – Business Card</title>
<link href="https://fonts.googleapis.com/css2?family=Oswald:wght@500;600&family=Open+Sans:wght@400&display=swap" rel="stylesheet">
<style>
  :root {
    --page-bg: #e6e6e6;
    --brand-blue: #1b4483;
    --card-white: #ffffff;
    --text-grey: #8a8a8a;
    --rule-grey: #9a9a9a;
    --icon-blue: #1b4483;
  }
  html, body {
    margin: 0;
    padding: 0;
    width: 1200px;
    height: 1000px;
    overflow: hidden;
    background: var(--page-bg);
  }
  .canvas {
    position: relative;
    width: 1200px;
    height: 1000px;
  }
  .card {
    position: absolute;
    left: 269px;
    width: 662px;
    height: 378px;
    box-shadow: 0 2px 6px rgba(0,0,0,0.25);
  }
  .card--front {
    top: 108px;
    background: var(--brand-blue);
  }
  .card--back {
    top: 521px;
    background: var(--card-white);
  }
  .brand-name {
    position: absolute;
    left: 0;
    right: 0;
    text-align: center;
    font-family: "Oswald", sans-serif;
    font-weight: 600;
    letter-spacing: 3px;
    margin: 0;
    display: flex;
    justify-content: center;
    align-items: center;
    gap: 14px;
  }
  .brand-name__square {
    width: 16px;
    height: 16px;
    display: inline-block;
  }
  .card--front .brand-name {
    top: 150px;
    font-size: 50px;
    color: var(--card-white);
  }
  .card--front .brand-name__square { background: var(--card-white); }
  .card--back .brand-name {
    top: 80px;
    font-size: 44px;
    color: var(--brand-blue);
  }
  .card--back .brand-name__square { background: var(--brand-blue); }

  .owner {
    position: absolute;
    right: calc(662px - 311px);
    top: 232px;
    text-align: right;
  }
  .owner__name {
    font-family: "Oswald", sans-serif;
    font-weight: 500;
    font-size: 30px;
    line-height: 36px;
    color: var(--brand-blue);
    margin: 0;
  }
  .owner__role {
    font-family: "Open Sans", sans-serif;
    font-size: 14px;
    color: var(--text-grey);
    margin: 0;
  }
  .divider {
    position: absolute;
    left: 327px;
    top: 236px;
    width: 1px;
    height: 51px;
    background: var(--rule-grey);
  }
  .contact-list {
    position: absolute;
    left: 346px;
    top: 231px;
    margin: 0;
    padding: 0;
    list-style: none;
    font-family: "Open Sans", sans-serif;
    font-size: 14px;
    color: var(--text-grey);
  }
  .contact-list li {
    display: flex;
    align-items: center;
    gap: 5px;
    height: 19px;
  }
  .contact-list svg { width: 11px; height: 11px; flex: none; }
  .address {
    position: absolute;
    left: 0;
    right: 0;
    top: 336px;
    text-align: center;
    font-family: "Open Sans", sans-serif;
    font-size: 15px;
    color: var(--text-grey);
    margin: 0;
  }
</style>
</head>
<body>
<main class="canvas">
  <section class="card card--front">
    <h1 class="brand-name"><span class="brand-name__square"></span>DUNMORE ROOFING</h1>
  </section>

  <section class="card card--back">
    <p class="brand-name"><span class="brand-name__square"></span>DUNMORE ROOFING</p>

    <div class="owner">
      <p class="owner__name">PAUL DUNMORE</p>
      <p class="owner__role">Owner</p>
    </div>
    <div class="divider"></div>

    <ul class="contact-list">
      <li>
        <svg viewBox="0 0 12 12" aria-hidden="true"><rect x="3" y="0.5" width="6" height="11" rx="1" fill="none" stroke="var(--icon-blue)" stroke-width="1.3"/><rect x="5" y="9" width="2" height="1" fill="var(--icon-blue)"/></svg>
        (613) 555-0147
      </li>
      <li>
        <svg viewBox="0 0 12 12" aria-hidden="true"><rect x="0.5" y="2.5" width="11" height="7" fill="var(--icon-blue)"/><path d="M0.5 2.5 L6 7 L11.5 2.5" fill="none" stroke="#fff" stroke-width="1"/></svg>
        paul@dunmoreroofing-example.com
      </li>
      <li>
        <svg viewBox="0 0 12 12" aria-hidden="true"><circle cx="6" cy="6" r="5.2" fill="none" stroke="var(--icon-blue)" stroke-width="1.2"/><ellipse cx="6" cy="6" rx="2.3" ry="5.2" fill="none" stroke="var(--icon-blue)" stroke-width="1"/><line x1="0.8" y1="6" x2="11.2" y2="6" stroke="var(--icon-blue)" stroke-width="1"/></svg>
        www.dunmoreroofing-example.com
      </li>
    </ul>

    <p class="address">Address: 4172 Township road 43 Plantagenet, ON K9X4T2</p>
  </section>
</main>
</body>
</html>
```